Business Card for a mobile physiotherapy company

I need a layout for a business card for a mobile physiotherapy company.
Slogan is "Mobile Physiotherapy - Your Road To Recovery"
Phone number is 867-555-0142
Email VardenTherapy@postnest.ca (subject to change with website)
Website www.VardenTherapy.ca
My name and credentials: Luke Varden Luke Varden, BSc(kin), MPT, CAFCI, IMS
Information maybe included: Direct Billing, Services including Physiotherapy, IMS, acupuncture
Maybe include facebook and instagram logos
One side with the logo clean and sharp
Other side with details, try not to look too busy, keep everything concise

```html
<!DOCTYPE html>
<html lang="en">
<head>
<meta charset="utf-8">
<title>Varden Therapy – Business Card</title>
<link href="https://fonts.googleapis.com/css2?family=Tinos:wght@700&family=Source+Sans+3:wght@400;600;700&display=swap" rel="stylesheet">
<style>
  :root{
    --navy:#2c4870;
    --green:#0b5a4a;
    --white:#ffffff;
    --rule:#c9c9c9;
    --ink:#1e1e1e;
    --bg-light:#e6e7e8;
    --bg-dark:#b4b5b8;
  }
  *{margin:0;padding:0;box-sizing:border-box}
  html,body{width:1200px;height:1113px;overflow:hidden}
  body{
    position:relative;
    background:linear-gradient(90deg,var(--bg-light),var(--bg-dark));
    font-family:"Source Sans 3",Arial,sans-serif;
  }
  .card{position:absolute;width:768px;height:439px;border-radius:26px;overflow:hidden}
  .card--front{left:361px;top:77px;background:var(--white);border:1px solid #6d6e71}
  .card--back{left:78px;top:584px;background:var(--navy)}

  /* front */
  .brand{position:absolute;text-align:center;font-family:"Tinos","Times New Roman",serif;font-weight:700;letter-spacing:.08em;line-height:1}
  .brand__dot{display:block;margin:0 auto 26px;border-radius:50%}
  .card--front .brand{left:52px;top:78px;width:300px;color:var(--navy)}
  .card--front .brand__dot{width:64px;height:64px;background:var(--navy)}
  .brand__name{font-size:52px;display:block}
  .brand__sub{font-size:30px;display:block;margin-top:18px;letter-spacing:.3em}
  .divider{position:absolute;left:392px;top:52px;width:3px;height:257px;background:var(--rule)}
  .details{position:absolute;left:494px;top:48px;width:260px}
  .details__name{font-family:"Tinos","Times New Roman",serif;font-weight:700;color:var(--navy);font-size:27px;letter-spacing:.04em;line-height:1}
  .details__creds{font-size:16px;color:var(--ink);margin-top:6px}
  .contact{list-style:none;margin-top:12px}
  .contact li{display:flex;align-items:center;gap:7px;font-size:19.5px;color:var(--ink);height:32.5px}
  .contact svg{width:19px;height:19px;flex:none}
  .services__title{font-weight:700;color:var(--navy);font-size:20.5px;margin-top:14px}
  .services{display:grid;grid-template-columns:auto auto;column-gap:14px;justify-content:start;list-style:none;margin-top:6px;color:var(--green);font-size:19.5px;line-height:28px}
  .services li::before{content:"•";font-size:13px;margin-right:5px;vertical-align:2px}
  .bands{position:absolute;left:0;right:0;top:351px}
  .bands__line{height:2px;background:var(--green)}
  .bands__strip{height:42px;margin:3px 0;background:var(--navy);color:var(--white);text-align:center;font-family:"Tinos","Times New Roman",serif;font-weight:700;font-size:19.5px;line-height:42px;letter-spacing:.02em}

  /* back */
  .card--back .brand{left:0;right:0;top:70px;color:var(--white)}
  .card--back .brand__dot{width:72px;height:72px;background:var(--white);margin-bottom:38px}
  .card--back .brand__name{font-size:60px}
  .card--back .brand__sub{font-size:32px;margin-top:20px}
  .socials{position:absolute;left:0;right:0;top:345px;display:flex;justify-content:center;gap:28px;color:var(--white);font-size:23.5px}
  .socials__item{display:flex;align-items:center;gap:12px}
  .socials__mark{width:48px;height:48px;border-radius:6px;background:var(--white)}
</style>
</head>
<body>

<section class="card card--front">
  <div class="brand">
    <span class="brand__dot"></span>
    <span class="brand__name">VARDEN</span>
    <span class="brand__sub">THERAPY</span>
  </div>

  <div class="divider"></div>

  <div class="details">
    <h1 class="details__name">LUKE VARDEN</h1>
    <p class="details__creds">BSc(kin), MPT, CAFCI, IMS</p>
    <ul class="contact">
      <li>
        <svg viewBox="0 0 20 20" aria-hidden="true"><circle cx="10" cy="10" r="8.6" fill="none" stroke="#2c4870" stroke-width="1.6"/><path d="M6.6 5.6l1.8-.4 1 2.3-1.1.9a6 6 0 0 0 3.3 3.3l.9-1.1 2.3 1-.4 1.8c-4.2.4-8.2-3.6-7.8-7.8z" fill="#2c4870"/></svg>
        867-555-0142
      </li>
      <li>
        <svg viewBox="0 0 20 20" aria-hidden="true"><circle cx="10" cy="10" r="8.6" fill="none" stroke="#2c4870" stroke-width="1.6"/><rect x="5.5" y="7" width="9" height="6.5" fill="#2c4870"/><path d="M5.5 7l4.5 3.5L14.5 7" fill="none" stroke="#fff" stroke-width="1"/></svg>
        VardenTherapy@postnest.ca
      </li>
      <li>
        <svg viewBox="0 0 20 20" aria-hidden="true"><g fill="none" stroke="#2c4870" stroke-width="1.3"><circle cx="10" cy="10" r="8.3"/><ellipse cx="10" cy="10" rx="3.8" ry="8.3"/><path d="M1.7 10h16.6M3 5.8h14M3 14.2h14M10 1.7v16.6"/></g></svg>
        www.VardenTherapy.ca
      </li>
    </ul>
    <h2 class="services__title">Services Including</h2>
    <ul class="services">
      <li>Physiotherapy</li>
      <li>Direct Billing</li>
      <li>Ims</li>
      <li>Acupuncture</li>
    </ul>
  </div>

  <div class="bands">
    <div class="bands__line"></div>
    <div class="bands__strip">Mobile Physiotherapy - Your Road To Recovery</div>
    <div class="bands__line"></div>
  </div>
</section>

<section class="card card--back">
  <div class="brand">
    <span class="brand__dot"></span>
    <span class="brand__name">VARDEN</span>
    <span class="brand__sub">THERAPY</span>
  </div>
  <div class="socials">
    <div class="socials__item"><span class="socials__mark"></span>VardenTherapy</div>
    <div class="socials__item"><span class="socials__mark"></span>@VardenTherapy</div>
  </div>
</section>

</body>
</html>
```